Business card for medical clinic

I need an upmarket, modern medical/health business card for my clinic

Contact Information for Business Card

name, address, email, qr code

```html
<!DOCTYPE html>
<html lang="en">
<head>
<meta charset="utf-8">
<title>Meridian Care Clinic – Business Card</title>
<link rel="stylesheet" href="https://fonts.googleapis.com/css2?family=Montserrat:wght@500;600;700&display=swap">
<style>
  :root {
    --stage: #2b2c2e;
    --navy: #1c2a4a;
    --navy-deep: #182440;
    --sky: #2aa9e0;
    --sky-mid: #3c8fbf;
    --ink: #141414;
    --paper: #ffffff;
  }
  * { margin: 0; padding: 0; box-sizing: border-box; }
  html, body { width: 1200px; height: 960px; overflow: hidden; }
  body {
    background: var(--stage);
    font-family: "Montserrat", sans-serif;
    display: flex;
    flex-direction: column;
    align-items: center;
    justify-content: center;
    gap: 40px;
  }
  .card {
    position: relative;
    width: 700px;
    height: 400px;
    border-radius: 22px;
    overflow: hidden;
    box-shadow: 0 14px 34px rgba(0,0,0,.45);
  }

  /* Front side */
  .card-front {
    background: linear-gradient(35deg, var(--sky) 0%, var(--sky-mid) 35%, var(--navy) 78%, var(--navy-deep) 100%);
    color: var(--paper);
  }
  .front-brand {
    position: absolute;
    left: 50%; top: 160px;
    transform: translateX(-50%);
    display: flex;
    align-items: center;
    gap: 22px;
  }
  .brand-ring {
    width: 92px; height: 92px;
    border-radius: 50%;
    border: 5px solid currentColor;
    flex: none;
  }
  .brand-name {
    font-weight: 600;
    letter-spacing: .12em;
    line-height: 1.15;
    text-transform: uppercase;
  }
  .front-brand .brand-name { font-size: 34px; }
  .front-web {
    position: absolute;
    left: 0; right: 0; bottom: 38px;
    display: flex; justify-content: center; align-items: center;
    gap: 8px;
    font-size: 15px; font-weight: 500;
  }

  /* Back side */
  .card-back { background: var(--paper); color: var(--ink); }
  .back-wave { position: absolute; inset: 0; }
  .back-brand {
    position: absolute; left: 44px; top: 40px;
    display: flex; align-items: center; gap: 16px;
    color: var(--navy);
  }
  .back-brand .brand-ring { width: 76px; height: 76px; border-width: 4px; }
  .back-brand .brand-name { font-size: 23px; }
  .holder {
    position: absolute; right: 44px; top: 26px;
    text-align: right;
  }
  .holder-name {
    color: var(--sky);
    font-weight: 700;
    font-size: 26px;
    letter-spacing: .01em;
  }
  .holder-title { font-size: 15px; font-weight: 500; margin-top: 2px; }
  .accent-bar {
    position: absolute; right: 0; top: 26px;
    width: 18px; height: 34px;
    background: var(--sky);
  }
  .address {
    position: absolute; right: 44px; top: 120px;
    text-align: right;
    font-size: 15px; font-weight: 500; line-height: 1.45;
  }
  .contact-list {
    position: absolute; left: 44px; top: 240px;
    list-style: none;
    font-size: 15px; font-weight: 500;
  }
  .contact-list li {
    display: flex; align-items: center; gap: 10px;
    height: 27px;
  }
  .contact-list svg { flex: none; }
</style>
</head>
<body>

  <section class="card card-front" aria-label="Card front">
    <div class="front-brand">
      <span class="brand-ring"></span>
      <span class="brand-name">Meridian Care<br>Clinic</span>
    </div>
    <p class="front-web">
      <svg width="16" height="16" viewBox="0 0 16 16" fill="none" stroke="#fff" stroke-width="1.3" aria-hidden="true">
        <circle cx="8" cy="8" r="6.5"/><ellipse cx="8" cy="8" rx="3" ry="6.5"/><line x1="1.5" y1="8" x2="14.5" y2="8"/>
      </svg>
      www.meridiancare.com
    </p>
  </section>

  <section class="card card-back" aria-label="Card back">
    <svg class="back-wave" viewBox="0 0 700 400" preserveAspectRatio="none" aria-hidden="true">
      <defs>
        <linearGradient id="waveFill" x1="0" y1="1" x2="1" y2="0">
          <stop offset="0" stop-color="#2aa9e0"/>
          <stop offset=".45" stop-color="#3a7fb0"/>
          <stop offset="1" stop-color="#1c2a4a"/>
        </linearGradient>
      </defs>
      <path d="M0,400 L0,388 C210,372 320,330 430,268 C530,212 610,196 700,192 L700,400 Z" fill="url(#waveFill)"/>
      <path d="M0,372 C210,358 320,316 430,254 C530,198 610,182 700,178" fill="none" stroke="url(#waveFill)" stroke-width="3"/>
    </svg>

    <div class="back-brand">
      <span class="brand-ring"></span>
      <span class="brand-name">Meridian Care<br>Clinic</span>
    </div>

    <span class="accent-bar"></span>
    <div class="holder">
      <p class="holder-name">DANA WHITFIELD</p>
      <p class="holder-title">Managing Director</p>
    </div>

    <p class="address">2480 Harbor Lane, Ste<br>210, Brookfield, TX 75390</p>

    <ul class="contact-list">
      <li>
        <svg width="16" height="16" viewBox="0 0 16 16" aria-hidden="true"><path d="M4 1.5l2.2 3-1.4 1.4a9 9 0 0 0 5.3 5.3l1.4-1.4 3 2.2-1.3 2.2C8 14.3 1.7 8 1.8 2.8z" fill="#2aa9e0"/></svg>
        555-014-2287
      </li>
      <li>
        <svg width="16" height="16" viewBox="0 0 16 16" aria-hidden="true"><rect x="1" y="3" width="14" height="10" rx="1" fill="#2aa9e0"/><path d="M1.5 3.5L8 9l6.5-5.5" fill="none" stroke="#fff" stroke-width="1.2"/></svg>
        hello@meridiancare.com
      </li>
      <li>
        <svg width="16" height="16" viewBox="0 0 16 16" aria-hidden="true"><circle cx="8" cy="8" r="7" fill="#2aa9e0"/><ellipse cx="8" cy="8" rx="3" ry="7" fill="none" stroke="#fff" stroke-width="1"/><line x1="1" y1="8" x2="15" y2="8" stroke="#fff" stroke-width="1"/></svg>
        www.meridiancare.com
      </li>
    </ul>
  </section>

</body>
</html>
```